High-Converting Facebook Ads for Portals Drapes & Louvres (6 Products)

We are looking for a graphic designer to create high-quality Facebook & Instagram ads for our business: Portals Drapes and Louvres (Melbourne, Australia).

We require 6 separate ad designs, each for a different product:

Zipscreen Blinds

Outdoor Awnings

Plantation Shutters

Roller Shutters

Security Doors

Roller Blinds & Sheer Curtains

Ad Specifications:

Sizes:

1440 x 1800 px (4:5 ratio)

1080 x 1080 px (1:1 ratio)

1080 x 1920 px (9:16 ratio for Stories/Reels)

Format: PNG (high resolution, not blurry)

Designed specifically for Meta (Facebook/Instagram ads)

Mobile-friendly layout (clear, easy to read)

Style:

Bold, sales-driven, retail-style ads (NOT minimal)

Eye-catching and designed to generate leads

Clean, professional layout

Similar to promotional home improvement ads

Brand Colours:

Red: #E31E24

Blue: #0072BC

White backgrounds

Each ad must include:

“SALE NOW ON” banner at top

Our showroom address:
482 Upper Wattleby Road, Kestrel Heights (must be fully visible, not cut off)

Phone number: 9471 2658

Our logo (provided)

Badge: “Celebrating 13 YEARS in Business” (must be clean and readable)

Call to Action:

For 5 ads: “Book a FREE quote TODAY!”

For Security Doors ad: “ORDER NOW”

Offers / Pricing:

Most products: “UP TO 40% OFF”

Plantation Shutters: “FROM $299/sqm”

Security Doors: “FROM $750”

Content for each ad (examples):

Zipscreen Blinds:

Made to Measure

Fully Installed

Wind, Sun & Insect Protection

Outdoor Awnings:

Reduce Heat & Glare

Energy Saving

Custom Made

Plantation Shutters:

Modern & Elegant

Light & Privacy Control

Durable & Easy Care

Roller Shutters:

Security Protection

Block Heat & Noise

Total Light Control

Security Doors:

3 Point Locking

Premium Mesh

Custom Made

Blinds & Sheers:

Huge Range of Fabrics

Modern Soft Finish

Perfect for Any Room

Important Notes:

All text must be sharp and easy to read (no blur)

Layout must be balanced and not overcrowded

Ensure no text is cut off (especially address and headings)

Badge text must be straight and professional (no distortion)

Use high-quality, relevant images (we will provide references)

Goal:
Create ads that look professional, trustworthy, and generate enquiries/bookings for in-home quotes.

We are open to creative ideas but want a strong, bold retail-style ad that converts.
I have uploaed chatgpt mocks

Target Market(s)

Homeowners in Melbourne, Australia (typically aged 30–65) looking to improve their homes with blinds, shutters, awnings and security doors. Mid to high income households focused on quality, security, and modern home upgrades.

Industry/Entity Type

Home Improvement / Construction / Retail

Font styles to use
Sans Serif

Requirements
Must have
• Clear, bold and easy-to-read text (must be readable on mobile) High-quality, non-blurry design Strong “SALE” style layout (retail promotional look) Proper spacing (no overcrowded designs) All key info visible (address must NOT be cut off) Correct pricing and offers included Clean “13 YEARS” badge (no distortion or curved text) Consistent branding across all 6 ads
Nice to have
• Modern, slightly premium feel while still being bold Good use of contrast (red/blue/white) Subtle shadows or layering to improve depth Clean use of icons or bullet points Strong hierarchy (headline → benefits → offer → CTA) Variations in layout for testing different ad styles
Should not have
• Minimal or plain designs (we want bold, sales-driven ads) Hard-to-read fonts or script fonts Low-quality or blurry images Overcrowded layouts with too much text Important text cut off (especially address or headings) Overuse of effects or “cheap” looking graphics Yellow-heavy colour schemes (must follow brand colours)

```html
<!DOCTYPE html>
<html lang="en">
<head>
<meta charset="utf-8">
<title>Portals Drapes &amp; Louvres – Sale Ads 1080 x 1080</title>
<link rel="stylesheet" href="https://fonts.googleapis.com/css2?family=Oswald:wght@400;500;600;700&family=PT+Serif:wght@700&family=Archivo+Black&display=swap">
<style>
  :root{
    --brand-red:#E31E24;
    --brand-blue:#0072BC;
    --white:#ffffff;
    --ink:#1d1d1d;
    --board:#2a2a2a;
    --title-font:"Oswald", sans-serif;
    --serif-font:"PT Serif", serif;
    --phone-font:"Archivo Black", sans-serif;
  }
  *{margin:0;padding:0;box-sizing:border-box}
  html,body{width:1200px;height:948px;overflow:hidden;background:var(--board)}
  .board{position:relative;width:1200px;height:948px;background:var(--board)}
  .board-title{position:absolute;top:98px;left:0;width:1200px;text-align:center;color:var(--white);font:700 25px/1 var(--title-font);letter-spacing:.2px}

  .ad{position:absolute;width:291px;height:291px;overflow:hidden;background:var(--white)}
  .ad-shapes{position:absolute;inset:0;width:291px;height:291px}
  .ad-shapes .red{fill:var(--brand-red)}
  .ad-shapes .blue{fill:var(--brand-blue)}
  .ad-shapes .white{fill:var(--white)}

  .brand{position:absolute;left:0;top:6px;width:103px;text-align:center;color:var(--brand-blue);font:500 10px/1.15 var(--title-font)}
  .brand-mark{display:block;width:12px;height:12px;margin:0 auto 3px;background:var(--brand-red)}

  .product{position:absolute;left:13px;top:58px;color:var(--white);font:500 19px/1.1 var(--title-font)}
  .benefits{position:absolute;left:17px;top:109px;list-style:none;color:var(--ink);font:500 8.2px/12.5px var(--title-font)}
  .benefits li{position:relative;padding-left:9px}
  .benefits li::before{content:"";position:absolute;left:0;top:3.5px;width:5px;height:5px;background:var(--brand-red)}
  .ad--indent .product{left:22px}
  .ad--indent .benefits{left:25px}

  .cta{position:absolute;left:12px;top:158px;color:var(--white);font:500 14px/1 var(--title-font)}
  .cta--order{left:21px;top:157px;font:700 17px/1 var(--serif-font);letter-spacing:.3px}

  .headline{position:absolute;left:108px;width:182px;text-align:center;color:var(--white);font:700 33px/1 var(--serif-font)}
  .headline--sale{top:8px}
  .headline--now{top:41px}

  .offer-label{position:absolute;color:var(--white);font:700 11px/1 var(--serif-font)}
  .offer-big{position:absolute;color:var(--white);font:700 52px/1 var(--title-font)}
  .offer-pct{position:absolute;left:228px;top:82px;color:var(--white);font:700 30px/1 var(--title-font)}
  .offer-off{position:absolute;left:231px;top:113px;color:var(--white);font:700 15px/1 var(--title-font);letter-spacing:.5px}
  .offer-unit{position:absolute;right:24px;top:118px;color:var(--white);font:700 14px/1 var(--title-font)}

  .badge{position:absolute;left:206px;top:149px;width:70px;text-align:center;color:var(--white)}
  .badge-top{display:block;font:600 5.2px/1 var(--title-font);letter-spacing:.4px;margin-top:6px}
  .badge-num{display:block;font:400 23px/1 var(--phone-font);margin-top:2px}
  .badge-years{display:block;font:700 9px/1 var(--serif-font);letter-spacing:.6px;margin-top:1px}
  .badge-sub{display:block;font:400 4.6px/1 var(--title-font);margin-top:2px}

  .photo{position:absolute;left:0;top:182px;width:291px;height:109px}
  .photo--zipscreen{background:linear-gradient(100deg,#8fa4b6 0%,#6f7376 35%,#5f6467 65%,#c9c9c7 100%)}
  .photo--awning{background:linear-gradient(160deg,#8fb4dc 0%,#b9d0e8 40%,#e9ecef 70%,#9aa3ab 100%)}
  .photo--shutters{background:linear-gradient(90deg,#c2c6cb 0%,#e6e8ea 40%,#b8bcc1 75%,#d5d8db 100%)}
  .photo--roller{background:linear-gradient(90deg,#dcdfe2 0%,#f2f3f4 45%,#cfd3d6 75%,#eef0f1 100%)}
  .photo--security{background:linear-gradient(180deg,#6f8b9c 0%,#7a6a4f 45%,#4f6b2e 75%,#3c4f25 100%)}
  .photo--sheers{background:linear-gradient(90deg,#f1efec 0%,#8b8278 35%,#6e655c 60%,#b9b2a9 85%,#e9e6e2 100%)}

  .phone{position:absolute;left:16px;top:247px;display:flex;align-items:center;gap:5px;color:var(--white);font:400 21px/1 var(--phone-font);letter-spacing:.3px}
  .phone svg{width:11px;height:11px;fill:var(--white)}
  .address{position:absolute;left:19px;top:275px;display:flex;align-items:center;gap:5px;color:var(--white);font:500 10px/1 var(--title-font)}
  .address svg{width:9px;height:10px}
</style>
</head>
<body>
<main class="board">
  <h1 class="board-title">1080 x 1080 px (1:1 ratio)</h1>

  <!-- Zipscreen Blinds -->
  <article class="ad" style="left:141px;top:203px">
    <div class="photo photo--zipscreen" role="img" aria-label="Grey zipscreen blinds lowered on a brick home patio"></div>
    <svg class="ad-shapes" viewBox="0 0 525 525" aria-hidden="true">
      <rect class="blue" x="0" y="102" width="320" height="84"/>
      <rect class="blue" x="0" y="276" width="400" height="52"/>
      <path class="blue" d="M186,0H525V310C480,350 420,350 340,340C250,328 186,262 186,150Z"/>
      <path class="red" d="M186,0H525V195C490,280 420,310 350,310C260,310 186,240 186,150Z"/>
      <circle class="blue" cx="434" cy="331" r="90"/>
      <circle class="white" cx="434" cy="331" r="77"/>
      <circle class="red" cx="434" cy="331" r="60"/>
      <path class="red" d="M0,440H266L301,492H0Z"/>
      <path class="blue" d="M0,492H372L416,525H0Z"/>
    </svg>
    <div class="brand"><span class="brand-mark"></span>Portals Drapes<br>&amp; Louvres</div>
    <h2 class="product">Zipscreen<br>Blinds</h2>
    <ul class="benefits"><li>Made to Measure</li><li>Fully Installed</li><li>Wind, Sun &amp; Insect Protection</li></ul>
    <p class="cta">Book a FREE quote TODAY!</p>
    <p class="headline headline--sale">SALE</p>
    <p class="headline headline--now">NOW ON</p>
    <span class="offer-label" style="left:128px;top:91px">UP TO</span>
    <span class="offer-big" style="left:170px;top:84px">40</span>
    <span class="offer-pct">%</span><span class="offer-off">OFF</span>
    <div class="badge"><span class="badge-top">CELEBRATING</span><span class="badge-num">13</span><span class="badge-years">YEARS</span><span class="badge-sub">in Business</span></div>
    <p class="phone"><svg viewBox="0 0 24 24"><path d="M6.6 10.8a15.1 15.1 0 0 0 6.6 6.6l2.2-2.2a1 1 0 0 1 1-.25 11.4 11.4 0 0 0 3.6.57 1 1 0 0 1 1 1V20a1 1 0 0 1-1 1A17 17 0 0 1 3 4a1 1 0 0 1 1-1h3.5a1 1 0 0 1 1 1c0 1.25.2 2.450.57 3.57a1 1 0 0 1-.25 1Z"/></svg>9471 2658</p>
    <p class="address"><svg viewBox="0 0 18 20"><path d="M9 1a6 6 0 0 0-6 6c0 4.5 6 10 6 10s6-5.5 6-10a6 6 0 0 0-6-6Z" fill="none" stroke="#fff" stroke-width="2"/><circle cx="9" cy="7" r="2" fill="#fff"/></svg>482 Upper Wattleby Road, Kestrel Heights</p>
  </article>

  <!-- Outdoor Awnings -->
  <article class="ad" style="left:454px;top:203px">
    <div class="photo photo--awning" role="img" aria-label="Striped outdoor awning over a weatherboard house under blue sky"></div>
    <svg class="ad-shapes" viewBox="0 0 525 525" aria-hidden="true">
      <rect class="blue" x="0" y="102" width="320" height="84"/>
      <rect class="blue" x="0" y="276" width="400" height="52"/>
      <path class="blue" d="M186,0H525V310C480,350 420,350 340,340C250,328 186,262 186,150Z"/>
      <path class="red" d="M186,0H525V195C490,280 420,310 350,310C260,310 186,240 186,150Z"/>
      <circle class="blue" cx="434" cy="331" r="90"/>
      <circle class="white" cx="434" cy="331" r="77"/>
      <circle class="red" cx="434" cy="331" r="60"/>
      <path class="red" d="M0,440H266L301,492H0Z"/>
      <path class="blue" d="M0,492H372L416,525H0Z"/>
    </svg>
    <div class="brand"><span class="brand-mark"></span>Portals Drapes<br>&amp; Louvres</div>
    <h2 class="product">Outdoor<br>Awnings</h2>
    <ul class="benefits"><li>Reduce Heat &amp; Glare</li><li>Energy Saving</li><li>Custom Made</li></ul>
    <p class="cta">Book a FREE quote TODAY!</p>
    <p class="headline headline--sale">SALE</p>
    <p class="headline headline--now">NOW ON</p>
    <span class="offer-label" style="left:128px;top:91px">UP TO</span>
    <span class="offer-big" style="left:170px;top:84px">40</span>
    <span class="offer-pct">%</span><span class="offer-off">OFF</span>
    <div class="badge"><span class="badge-top">CELEBRATING</span><span class="badge-num">13</span><span class="badge-years">YEARS</span><span class="badge-sub">in Business</span></div>
    <p class="phone"><svg viewBox="0 0 24 24"><path d="M6.6 10.8a15.1 15.1 0 0 0 6.6 6.6l2.2-2.2a1 1 0 0 1 1-.25 11.4 11.4 0 0 0 3.6.57 1 1 0 0 1 1 1V20a1 1 0 0 1-1 1A17 17 0 0 1 3 4a1 1 0 0 1 1-1h3.5a1 1 0 0 1 1 1c0 1.25.2 2.45.57 3.57a1 1 0 0 1-.25 1Z"/></svg>9471 2658</p>
    <p class="address"><svg viewBox="0 0 18 20"><path d="M9 1a6 6 0 0 0-6 6c0 4.5 6 10 6 10s6-5.5 6-10a6 6 0 0 0-6-6Z" fill="none" stroke="#fff" stroke-width="2"/><circle cx="9" cy="7" r="2" fill="#fff"/></svg>482 Upper Wattleby Road, Kestrel Heights</p>
  </article>

  <!-- Plantation Shutters -->
  <article class="ad" style="left:768px;top:203px">
    <div class="photo photo--shutters" role="img" aria-label="White plantation shutters on windows in a grey room"></div>
    <svg class="ad-shapes" viewBox="0 0 525 525" aria-hidden="true">
      <rect class="blue" x="0" y="102" width="320" height="84"/>
      <rect class="blue" x="0" y="276" width="400" height="52"/>
      <path class="blue" d="M186,0H525V310C480,350 420,350 340,340C250,328 186,262 186,150Z"/>
      <path class="red" d="M186,0H525V195C490,280 420,310 350,310C260,310 186,240 186,150Z"/>
      <circle class="blue" cx="434" cy="331" r="90"/>
      <circle class="white" cx="434" cy="331" r="77"/>
      <circle class="red" cx="434" cy="331" r="60"/>
      <path class="red" d="M0,440H266L301,492H0Z"/>
      <path class="blue" d="M0,492H372L416,525H0Z"/>
    </svg>
    <div class="brand"><span class="brand-mark"></span>Portals Drapes<br>&amp; Louvres</div>
    <h2 class="product">Plantation<br>Shutters</h2>
    <ul class="benefits"><li>Modern &amp; Elegant</li><li>Light &amp; Privacy Control</li><li>Durable &amp; Easy Care</li></ul>
    <p class="cta">Book a FREE quote TODAY!</p>
    <p class="headline headline--sale">SALE</p>
    <p class="headline headline--now">NOW ON</p>
    <span class="offer-label" style="left:130px;top:95px;font-size:13px">FROM</span>
    <span class="offer-big" style="left:174px;top:78px;font-size:40px">$299</span>
    <span class="offer-unit">/sqm</span>
    <div class="badge"><span class="badge-top">CELEBRATING</span><span class="badge-num">13</span><span class="badge-years">YEARS</span><span class="badge-sub">in Business</span></div>
    <p class="phone"><svg viewBox="0 0 24 24"><path d="M6.6 10.8a15.1 15.1 0 0 0 6.6 6.6l2.2-2.2a1 1 0 0 1 1-.25 11.4 11.4 0 0 0 3.6.57 1 1 0 0 1 1 1V20a1 1 0 0 1-1 1A17 17 0 0 1 3 4a1 1 0 0 1 1-1h3.5a1 1 0 0 1 1 1c0 1.25.2 2.45.57 3.57a1 1 0 0 1-.25 1Z"/></svg>9471 2658</p>
    <p class="address"><svg viewBox="0 0 18 20"><path d="M9 1a6 6 0 0 0-6 6c0 4.5 6 10 6 10s6-5.5 6-10a6 6 0 0 0-6-6Z" fill="none" stroke="#fff" stroke-width="2"/><circle cx="9" cy="7" r="2" fill="#fff"/></svg>482 Upper Wattleby Road, Kestrel Heights</p>
  </article>

  <!-- Roller Shutters -->
  <article class="ad" style="left:141px;top:514px">
    <div class="photo photo--roller" role="img" aria-label="Bright white interior with roller shutters on windows"></div>
    <svg class="ad-shapes" viewBox="0 0 525 525" aria-hidden="true">
      <rect class="blue" x="0" y="102" width="320" height="84"/>
      <rect class="blue" x="0" y="276" width="400" height="52"/>
      <path class="blue" d="M186,0H525V310C480,350 420,350 340,340C250,328 186,262 186,150Z"/>
      <path class="red" d="M186,0H525V195C490,280 420,310 350,310C260,310 186,240 186,150Z"/>
      <circle class="blue" cx="434" cy="331" r="90"/>
      <circle class="white" cx="434" cy="331" r="77"/>
      <circle class="red" cx="434" cy="331" r="60"/>
      <path class="red" d="M0,440H266L301,492H0Z"/>
      <path class="blue" d="M0,492H372L416,525H0Z"/>
    </svg>
    <div class="brand"><span class="brand-mark"></span>Portals Drapes<br>&amp; Louvres</div>
    <h2 class="product">Roller<br>Shutters</h2>
    <ul class="benefits"><li>Security Protection</li><li>Block Heat &amp; Noise</li><li>Total Light Control</li></ul>
    <p class="cta">Book a FREE quote TODAY!</p>
    <p class="headline headline--sale">SALE</p>
    <p class="headline headline--now">NOW ON</p>
    <span class="offer-label" style="left:128px;top:91px">UP TO</span>
    <span class="offer-big" style="left:170px;top:84px">40</span>
    <span class="offer-pct">%</span><span class="offer-off">OFF</span>
    <div class="badge"><span class="badge-top">CELEBRATING</span><span class="badge-num">13</span><span class="badge-years">YEARS</span><span class="badge-sub">in Business</span></div>
    <p class="phone"><svg viewBox="0 0 24 24"><path d="M6.6 10.8a15.1 15.1 0 0 0 6.6 6.6l2.2-2.2a1 1 0 0 1 1-.25 11.4 11.4 0 0 0 3.6.57 1 1 0 0 1 1 1V20a1 1 0 0 1-1 1A17 17 0 0 1 3 4a1 1 0 0 1 1-1h3.5a1 1 0 0 1 1 1c0 1.25.2 2.45.57 3.57a1 1 0 0 1-.25 1Z"/></svg>9471 2658</p>
    <p class="address"><svg viewBox="0 0 18 20"><path d="M9 1a6 6 0 0 0-6 6c0 4.5 6 10 6 10s6-5.5 6-10a6 6 0 0 0-6-6Z" fill="none" stroke="#fff" stroke-width="2"/><circle cx="9" cy="7" r="2" fill="#fff"/></svg>482 Upper Wattleby Road, Kestrel Heights</p>
  </article>

  <!-- Security Doors -->
  <article class="ad ad--indent" style="left:454px;top:514px">
    <div class="photo photo--security" role="img" aria-label="Security screen door opening onto a garden with water view"></div>
    <svg class="ad-shapes" viewBox="0 0 525 525" aria-hidden="true">
      <rect class="blue" x="0" y="102" width="320" height="84"/>
      <rect class="blue" x="0" y="276" width="400" height="52"/>
      <path class="blue" d="M186,0H525V310C480,350 420,350 340,340C250,328 186,262 186,150Z"/>
      <path class="red" d="M186,0H525V195C490,280 420,310 350,310C260,310 186,240 186,150Z"/>
      <circle class="blue" cx="434" cy="331" r="90"/>
      <circle class="white" cx="434" cy="331" r="77"/>
      <circle class="red" cx="434" cy="331" r="60"/>
      <path class="red" d="M0,440H266L301,492H0Z"/>
      <path class="blue" d="M0,492H372L416,525H0Z"/>
    </svg>
    <div class="brand"><span class="brand-mark"></span>Portals Drapes<br>&amp; Louvres</div>
    <h2 class="product">Security<br>Doors</h2>
    <ul class="benefits"><li>3 Point Locking</li><li>Premium Mesh</li><li>Custom Made</li></ul>
    <p class="cta cta--order">ORDER NOW</p>
    <p class="headline headline--sale">SALE</p>
    <p class="headline headline--now">NOW ON</p>
    <span class="offer-label" style="left:130px;top:99px;font-size:13px">FROM</span>
    <span class="offer-big" style="left:176px;top:82px;font-size:44px">$750</span>
    <div class="badge"><span class="badge-top">CELEBRATING</span><span class="badge-num">13</span><span class="badge-years">YEARS</span><span class="badge-sub">in Business</span></div>
    <p class="phone"><svg viewBox="0 0 24 24"><path d="M6.6 10.8a15.1 15.1 0 0 0 6.6 6.6l2.2-2.2a1 1 0 0 1 1-.25 11.4 11.4 0 0 0 3.6.57 1 1 0 0 1 1 1V20a1 1 0 0 1-1 1A17 17 0 0 1 3 4a1 1 0 0 1 1-1h3.5a1 1 0 0 1 1 1c0 1.25.2 2.45.57 3.57a1 1 0 0 1-.25 1Z"/></svg>9471 2658</p>
    <p class="address"><svg viewBox="0 0 18 20"><path d="M9 1a6 6 0 0 0-6 6c0 4.5 6 10 6 10s6-5.5 6-10a6 6 0 0 0-6-6Z" fill="none" stroke="#fff" stroke-width="2"/><circle cx="9" cy="7" r="2" fill="#fff"/></svg>482 Upper Wattleby Road, Kestrel Heights</p>
  </article>

  <!-- Blinds & Sheers -->
  <article class="ad" style="left:768px;top:514px">
    <div class="photo photo--sheers" role="img" aria-label="Soft grey sheer curtains over a window"></div>
    <svg class="ad-shapes" viewBox="0 0 525 525" aria-hidden="true">
      <rect class="blue" x="0" y="102" width="320" height="84"/>
      <rect class="blue" x="0" y="276" width="400" height="52"/>
      <path class="blue" d="M186,0H525V310C480,350 420,350 340,340C250,328 186,262 186,150Z"/>
      <path class="red" d="M186,0H525V195C490,280 420,310 350,310C260,310 186,240 186,150Z"/>
      <circle class="blue" cx="434" cy="331" r="90"/>
      <circle class="white" cx="434" cy="331" r="77"/>
      <circle class="red" cx="434" cy="331" r="60"/>
      <path class="red" d="M0,440H266L301,492H0Z"/>
      <path class="blue" d="M0,492H372L416,525H0Z"/>
    </svg>
    <div class="brand"><span class="brand-mark"></span>Portals Drapes<br>&amp; Louvres</div>
    <h2 class="product">Blinds &amp;<br>Sheers</h2>
    <ul class="benefits"><li>Huge Range of Fabrics</li><li>Modern Soft Finish</li><li>Perfect for Any Room</li></ul>
    <p class="cta">Book a FREE quote TODAY!</p>
    <p class="headline headline--sale">SALE</p>
    <p class="headline headline--now">NOW ON</p>
    <span class="offer-label" style="left:128px;top:91px">UP TO</span>
    <span class="offer-big" style="left:170px;top:84px">40</span>
    <span class="offer-pct">%</span><span class="offer-off">OFF</span>
    <div class="badge"><span class="badge-top">CELEBRATING</span><span class="badge-num">13</span><span class="badge-years">YEARS</span><span class="badge-sub">in Business</span></div>
    <p class="phone"><svg viewBox="0 0 24 24"><path d="M6.6 10.8a15.1 15.1 0 0 0 6.6 6.6l2.2-2.2a1 1 0 0 1 1-.25 11.4 11.4 0 0 0 3.6.57 1 1 0 0 1 1 1V20a1 1 0 0 1-1 1A17 17 0 0 1 3 4a1 1 0 0 1 1-1h3.5a1 1 0 0 1 1 1c0 1.25.2 2.45.57 3.57a1 1 0 0 1-.25 1Z"/></svg>9471 2658</p>
    <p class="address"><svg viewBox="0 0 18 20"><path d="M9 1a6 6 0 0 0-6 6c0 4.5 6 10 6 10s6-5.5 6-10a6 6 0 0 0-6-6Z" fill="none" stroke="#fff" stroke-width="2"/><circle cx="9" cy="7" r="2" fill="#fff"/></svg>482 Upper Wattleby Road, Kestrel Heights</p>
  </article>
</main>
</body>
</html>
```